Harborview Estates Business Card for Apartment Buildings

Create business cards for resident managers who run apartment buildings. The audience is the public who are searching for apartment rentals, and current residents who live at the apartment building. Key design element will be incorporating the company logo, however, the logo cannot dominate. The building name and manager name are more important than the logo. Current business card design leaves little room for copy, so we may need to reduce the size on the current card to allow for more space for copy.

Target Market(s)

Adults 18-65 years of age, who are looking for an apartment rental, plus current residents who live at our apartment buildings.

Industry/Entity Type

Property Management

Contact Information for Business Card

A major design element will be use of the company logo. Important property and manager contact information must be part of the design. The size of the logo will need to be reduced to make room for building and manager contact copy.

Font styles to use
Sans Serif

Colors
3176b5
000000
959595
ffffff

Requirements
Must have
• 1) Incorporate the company logo.
• 2) Use the company colors (dark blue, black/grey, over white).
• 3) FEATURE THE BUILDING NAME
• 4) FEATURE THE MANAGER NAME
• 5) The company name is less important than BUILDING and MANAGER
• 6) Manager contact information
• **SEE ATTACHED CREATIVE BRIEF**
Nice to have
• 1) Back of card logo watermark
• 2) Ability to write notes on back of carfd
Should not have
• Avoid letting the company logo dominate the card, the building name and manager are more important than the company logo.

```html
<!DOCTYPE html>
<html lang="en">
<head>
<meta charset="utf-8">
<title>Harborview Estates – Resident Manager Business Card</title>
<link rel="stylesheet" href="https://fonts.googleapis.com/css2?family=Fira+Sans:wght@400;600&display=swap">
<style>
  :root {
    --brand-blue: #1f6aa8;
    --ink-grey: #4a4a4c;
    --text-grey: #5c5c5c;
    --backdrop: #9a9a9a;
    --card-front: #ffffff;
    --card-back: #e3e5e5;
  }
  * { box-sizing: border-box; margin: 0; padding: 0; }
  html, body {
    width: 1200px; height: 1200px; overflow: hidden;
    background: var(--backdrop);
    font-family: "Fira Sans", Arial, sans-serif;
  }
  .canvas { position: relative; width: 1200px; height: 1200px; }
  .card {
    position: absolute; left: 206px; width: 790px; height: 450px;
  }
  .card--front { top: 94px; background: var(--card-front); }
  .card--back { top: 656px; background: var(--card-back); }

  .company-mark {
    position: absolute; left: 40px; top: 170px;
    display: flex; align-items: center; gap: 18px;
  }
  .company-mark__square {
    width: 46px; height: 46px; background: var(--brand-blue);
  }
  .company-mark__name {
    color: var(--brand-blue); font-weight: 600; font-size: 34px;
    line-height: 1.1; letter-spacing: 0.5px;
  }

  .property {
    position: absolute; right: 53px; top: 48px; text-align: right;
  }
  .property__name {
    color: var(--brand-blue); font-weight: 600; font-size: 23px;
    letter-spacing: 0.6px; text-transform: uppercase;
  }
  .property__address {
    color: var(--text-grey); font-size: 18px; line-height: 32px; margin-top: 2px;
  }
  .manager {
    position: absolute; right: 53px; top: 176px; text-align: right;
  }
  .manager__name { color: var(--brand-blue); font-weight: 600; font-size: 31px; }
  .manager__role { color: var(--text-grey); font-size: 18px; margin-top: 4px; }
  .accent-bar {
    position: absolute; right: 0; top: 184px; width: 10px; height: 64px;
    background: var(--brand-blue);
  }
  .contact-list {
    position: absolute; right: 46px; top: 280px; list-style: none;
  }
  .contact-list li {
    display: flex; justify-content: flex-end; align-items: center;
    height: 31px; color: var(--text-grey); font-size: 18px;
  }
  .contact-list svg { width: 18px; height: 18px; margin-left: 16px; flex: none; }

  .back-mark {
    position: absolute; left: 0; right: 0; top: 196px;
    display: flex; justify-content: center; align-items: center; gap: 16px;
  }
  .back-mark__square { width: 40px; height: 40px; background: var(--brand-blue); }
  .back-mark__name {
    color: var(--brand-blue); font-weight: 600; font-size: 36px; letter-spacing: 1px;
    text-transform: uppercase;
  }
  .website {
    position: absolute; left: 0; right: 0; top: 396px; text-align: center;
    color: var(--brand-blue); font-size: 17px; letter-spacing: 1.2px;
  }
</style>
</head>
<body>
<main class="canvas">
  <section class="card card--front">
    <div class="company-mark">
      <span class="company-mark__square"></span>
      <span class="company-mark__name">Harborview<br>Estates</span>
    </div>

    <div class="property">
      <h1 class="property__name">Cedar Point Apartments</h1>
      <p class="property__address">2480 Linden Avenue Bay<br>City, CA 90210</p>
    </div>

    <div class="manager">
      <h2 class="manager__name">Marisol Ortega</h2>
      <p class="manager__role">Resident Manager</p>
    </div>
    <span class="accent-bar"></span>

    <ul class="contact-list">
      <li>555-201-1400
        <svg viewBox="0 0 24 24" aria-label="Phone"><path fill="#1f6aa8" d="M6.6 10.8a15 15 0 0 0 6.6 6.6l2.2-2.2c.3-.3.7-.4 1-.2 1.1.4 2.3.6 3.6.6.6 0 1 .4 1 1V20c0 .6-.4 1-1 1A17 17 0 0 1 3 4c0-.6.4-1 1-1h3.5c.6 0 1 .4 1 1 0 1.3.2 2.5.6 3.6.1.3 0 .7-.2 1z"/></svg>
      </li>
      <li>555-201-1401
        <svg viewBox="0 0 24 24" aria-label="Fax"><path fill="#1f6aa8" d="M7 3h10v4H7zM4 8h16a2 2 0 0 1 2 2v6h-4v5H6v-5H2v-6a2 2 0 0 1 2-2zm4 8v3h8v-3z"/></svg>
      </li>
      <li>555-201-1402
        <svg viewBox="0 0 24 24" aria-label="Mobile"><rect x="6.5" y="2" width="11" height="20" rx="2" fill="none" stroke="#1f6aa8" stroke-width="2"/><circle cx="12" cy="18" r="1.2" fill="#1f6aa8"/></svg>
      </li>
      <li>marisol@harborviewest.com
        <svg viewBox="0 0 24 24" aria-label="Email"><rect x="2.5" y="5" width="19" height="14" fill="none" stroke="#1f6aa8" stroke-width="1.8"/><path d="M2.5 5l9.5 8 9.5-8M2.5 19l7-6.5M21.5 19l-7-6.5" fill="none" stroke="#1f6aa8" stroke-width="1.6"/></svg>
      </li>
    </ul>
  </section>

  <section class="card card--back">
    <div class="back-mark">
      <span class="back-mark__square"></span>
      <span class="back-mark__name">Harborview Estates LLC</span>
    </div>
    <p class="website">www.harborviewestates.us</p>
  </section>
</main>
</body>
</html>
```